Dell Corvin - Acoustic Album Cover

I am a musical artist releasing my first full-length solo album. It is composed of nine original "percussive" acoustic fingerstyle songs. Some of my earlier recordings (not for this album) are available at http://www.tunelodge.net/dellcorvin for reference. I am looking for creative album art and need both a front cover and back cover/track listing for physical CD replication and online album art purposes. I am open to a more "natural" design using the pictures included in the uploaded files section or to a more artistic design that doesn't use any of the included pictures at all. The name of the album is "Driftwood", and artist is "Dell Corvin" (me). The track list is:

01) Orchard Shuffle
02) Tumbleweed
03) Glimpses of Perlow
04) Wound Up
05) Walk Along
06) The Quiet Ridge
07) Unfolding
08) Evening on Barrow Lane
09) Lucinda's Tune

Here are some album art examples from professional acoustic artists in the same style as a reference:

https://img.vidplexo.net/v/QwLmZr8NeYt/cover.jpg
http://strumvault.net/wp-content/uploads/2009/12/Low-Meadow-cover-reduced.jpg
https://plinkhouse.examplecdn.net/ImageGen.ashx?image=/media/10608/Teo-Bandry.jpg&width=500
https://files.openfolio.net/commons/1/11/Paul_Vesterby-Tidewater_album.jpg
https://direct.songrivet.net/imageserver/images/Alb.000000000/500x500.jpg
https://pics.shopvarlo.net/images/I/7Kq2mXwPzA1._SY355_.jpg
https://pics.shopvarlo.net/images/I/3Hn9bTyQcL4._SY355_.jpg

As you can see, there is a broad mix of both art-based and photograph-based album covers for artists of this style. I am open to either approach, and an example of each would be preferred if time permits.

Thank you for considering my project and for sharing your artistic talents!

-Dell

Target Market(s)

Music app listeners (Tunora, Melodex, Cadenzo) on any app which displays the album art as part of the artist information pane.

Industry/Entity Type

Music Download

Font styles to use
Serif
Sans Serif
Decorative

Colors

Designer to choose colors to be used in the design.

Requirements
Must have
• The project must have the album name and artist name on the front cover artwork, as well as the track listing on the back cover artwork.
Nice to have
• Some original, creative album artwork would be nice to have, but I would settle on well-done picture-based album designs (photos included) as well.
Should not have
• The project should not have too "stuffy" of a feel (similar to a lot of classical guitar album artwork which usually features the artist in a turtleneck smiling at the camera with guitar in lap).

```html
<!DOCTYPE html>
<html lang="en">
<head>
<meta charset="utf-8">
<title>Dell Corvin – Driftwood</title>
<link rel="stylesheet" href="https://fonts.googleapis.com/css2?family=Caveat:wght@700&display=swap">
<style>
  :root {
    --paper: #ffffff;
    --ink: #111111;
    --shirt-blue: #1f9ddc;
    --deep-blue: #0c5a8c;
    --wood-orange: #ee8f3e;
    --wood-brown: #9a4512;
    --fret-green: #6a9a3a;
  }
  html, body {
    margin: 0;
    padding: 0;
    width: 1200px;
    height: 1200px;
    overflow: hidden;
    background: var(--paper);
  }
  .cover {
    position: relative;
    width: 1200px;
    height: 1200px;
    background: var(--paper);
  }
  .cover-art {
    position: absolute;
    left: 0;
    top: 0;
    width: 1200px;
    height: 845px;
    display: block;
  }
  .cover-title {
    position: absolute;
    right: 88px;
    margin: 0;
    font-family: "Caveat", cursive;
    font-weight: 700;
    font-size: 68px;
    line-height: 1;
    letter-spacing: 0.3em;
    margin-right: -0.3em;
    color: var(--ink);
    text-transform: uppercase;
    white-space: nowrap;
    transform: skewX(-8deg);
    transform-origin: right bottom;
  }
  .artist-name { top: 888px; }
  .album-name { top: 1000px; }
</style>
</head>
<body>
  <main class="cover">
    <svg class="cover-art" viewBox="0 0 1200 845" preserveAspectRatio="none" role="img"
         aria-label="Posterized high-contrast photo of a guitarist in a blue shirt playing an acoustic guitar, its neck and tuning pegs reaching to the right">
      <defs>
        <radialGradient id="woodGlow" cx="0.22" cy="0.5" r="0.42">
          <stop offset="0" stop-color="var(--wood-orange)" stop-opacity="0.95"/>
          <stop offset="0.55" stop-color="var(--wood-brown)" stop-opacity="0.55"/>
          <stop offset="1" stop-color="var(--wood-orange)" stop-opacity="0"/>
        </radialGradient>
        <radialGradient id="shirtGlow" cx="0.55" cy="0.2" r="0.4">
          <stop offset="0" stop-color="var(--shirt-blue)" stop-opacity="0.95"/>
          <stop offset="0.6" stop-color="var(--deep-blue)" stop-opacity="0.45"/>
          <stop offset="1" stop-color="var(--shirt-blue)" stop-opacity="0"/>
        </radialGradient>
        <radialGradient id="pegGlow" cx="0.92" cy="0.62" r="0.3">
          <stop offset="0" stop-color="var(--deep-blue)" stop-opacity="0.8"/>
          <stop offset="1" stop-color="var(--shirt-blue)" stop-opacity="0"/>
        </radialGradient>
        <linearGradient id="neckBand" x1="0" y1="0" x2="1" y2="0">
          <stop offset="0" stop-color="var(--wood-orange)" stop-opacity="0.7"/>
          <stop offset="0.5" stop-color="var(--fret-green)" stop-opacity="0.55"/>
          <stop offset="1" stop-color="var(--wood-brown)" stop-opacity="0.6"/>
        </linearGradient>
        <linearGradient id="lowerFade" x1="0" y1="0" x2="0" y2="1">
          <stop offset="0.7" stop-color="#fff" stop-opacity="0"/>
          <stop offset="1" stop-color="#fff" stop-opacity="0.85"/>
        </linearGradient>
      </defs>
      <rect width="1200" height="845" fill="var(--paper)"/>
      <rect width="1200" height="845" fill="url(#shirtGlow)"/>
      <rect width="1200" height="845" fill="url(#pegGlow)"/>
      <rect width="1200" height="845" fill="url(#woodGlow)"/>
      <rect y="300" width="1200" height="130" fill="url(#neckBand)" opacity="0.8"/>
      <rect width="1200" height="845" fill="url(#lowerFade)"/>
    </svg>

    <h1 class="cover-title artist-name">Dell Corvin</h1>
    <h2 class="cover-title album-name">Driftwood</h2>
  </main>
</body>
</html>
```